4th Generation Family Business Needs a New Card Design!

We are a family owned 4th Generation company. We are based in the Sydney, Australia area and we are desperately in need of a more modern and classy card. We are monumental masons who design, supply & erect lasting memorials throughout cemeteries in Sydney. Our customers are normally in a period of grieving. I have attached logo files that will need to be implemented on the card. Company was established 1935. Australian Owned and Operated. Card needs to be designed to PIXO.com specification.

Target Market(s)

Our target market is based upon people that a grieving for family members that have passed away. We also deal with alot of companies that own and operate cemeteries.

Industry/Entity Type

Business

Contact Information for Business Card

Simon Harcourt, Operations Manager, 0417293086, simon@harcourtmemorials.com.au
Lewis Harcourt, Director, 0491630572, lewis@harcourtmemorials.com.au
Phone # 02 9561 3048
Website: www.harcourtmemorials.com.au
Address: Suite 17, 8 Palfrey Lane, West Carlow, Sydney NSW 2156

Font styles to use
Serif
Decorative
Script

Requirements
Must have
• Would like to see the logo nicely implemented with a modern design. Embossed lettering would be a nice additive.

```html
<!DOCTYPE html>
<html lang="en">
<head>
<meta charset="utf-8">
<title>Harcourt Memorials – Business Card</title>
<link rel="stylesheet" href="https://fonts.googleapis.com/css2?family=Arimo:wght@400;700&display=swap">
<style>
  :root {
    --page-bg: #ecebe7;
    --card-white: #ffffff;
    --charcoal-top: #4a4a4c;
    --charcoal-bottom: #1f1f21;
    --ink: #1c1c1c;
    --gold: #e9bd2a;
    --gold-deep: #e2b321;
    --soft-white: #f1f1f1;
    --muted: #d9d9d9;
  }
  html, body {
    margin: 0;
    padding: 0;
    width: 1200px;
    height: 950px;
    overflow: hidden;
    background: var(--page-bg);
    font-family: "Arimo", Arial, sans-serif;
  }
  .canvas {
    position: relative;
    width: 1200px;
    height: 950px;
  }
  .card {
    position: absolute;
    top: 115px;
    width: 440px;
    height: 720px;
    overflow: hidden;
    box-shadow: 0 6px 18px rgba(0,0,0,0.18);
  }
  .card-front { left: 120px; background: var(--card-white); }
  .card-back  { left: 640px; background: var(--gold); }

  /* front: upper white area with headstone frame */
  .front-top {
    position: absolute;
    inset: 0 0 auto 0;
    height: 330px;
  }
  .headstone-frame {
    position: absolute;
    left: 0; top: 0;
    width: 440px; height: 330px;
  }
  .brand {
    position: absolute;
    left: 0; right: 0;
    text-align: center;
    color: var(--ink);
    font-weight: 700;
  }
  .brand-front { top: 150px; }
  .brand-mark {
    display: block;
    width: 34px; height: 34px;
    margin: 0 auto 14px;
    background: currentColor;
  }
  .brand-name {
    display: block;
    font-size: 40px;
    letter-spacing: 3px;
    line-height: 1;
  }
  .brand-sub {
    display: block;
    margin-top: 8px;
    font-size: 20px;
    letter-spacing: 6px;
  }

  /* front: lower charcoal contact panel */
  .contact-panel {
    position: absolute;
    left: 0; right: 0; bottom: 0;
    height: 390px;
    background: linear-gradient(160deg, var(--charcoal-top), var(--charcoal-bottom));
    color: var(--soft-white);
    text-align: right;
    padding: 40px 36px 0 0;
    box-sizing: border-box;
  }
  .contact-name {
    margin: 0;
    font-size: 25px;
    font-weight: 700;
    color: var(--gold);
  }
  .contact-role {
    margin: 4px 0 26px;
    font-size: 20px;
    color: var(--muted);
  }
  .contact-lines {
    margin: 0;
    padding: 0;
    list-style: none;
    font-size: 18px;
    line-height: 1.55;
  }
  .contact-label {
    color: var(--gold);
    font-weight: 700;
  }

  /* back */
  .brand-back {
    top: 260px;
    color: var(--card-white);
  }
  .back-web {
    position: absolute;
    left: 0; right: 0; bottom: 60px;
    text-align: center;
    font-size: 17px;
    letter-spacing: 1px;
    color: var(--card-white);
  }
</style>
</head>
<body>
<main class="canvas">

  <section class="card card-front" aria-label="Business card front">
    <div class="front-top">
      <svg class="headstone-frame" viewBox="0 0 440 330" aria-hidden="true">
        <path d="M40 330 V92 H62 V62 H92 V40 H348 V62 H378 V92 H400 V330"
              fill="none" stroke="#1c1c1c" stroke-width="5"/>
      </svg>
      <div class="brand brand-front">
        <span class="brand-mark"></span>
        <span class="brand-name">HARCOURT</span>
        <span class="brand-sub">MEMORIALS</span>
      </div>
    </div>

    <div class="contact-panel">
      <p class="contact-name">Simon Harcourt</p>
      <p class="contact-role">Operations Manager</p>
      <ul class="contact-lines">
        <li>Suite 17, 8 Palfrey Lane</li>
        <li>West Carlow, Sydney NSW 2156</li>
        <li><span class="contact-label">P :</span> 02 9561 3048</li>
        <li><span class="contact-label">M :</span> 0417293086</li>
        <li>simon@harcourtmemorials.com.au</li>
        <li>www.harcourtmemorials.com.au</li>
      </ul>
    </div>
  </section>

  <section class="card card-back" aria-label="Business card back">
    <div class="brand brand-back">
      <span class="brand-mark"></span>
      <span class="brand-name">HARCOURT</span>
      <span class="brand-sub">MEMORIALS</span>
    </div>
    <p class="back-web">www.harcourtmemorials.com.au</p>
  </section>

</main>
</body>
</html>
```